Website for new dental office

I am Dr. Colin Ashford and am building a new dental practice. I specialize in general dentistry. I am young and have a higher end dental practice incorporating very new technologies and would like my website to reflect that. As many dental patients are older, the website must be very easy to navigate. I would like patients to be able to request appointments, and will eventually add on patient information forms (the health history, etc, that you normally fill out in the practice) from my practice management software, so leave an area for that.

Industry/Entity Type

Building

```html
<!DOCTYPE html>
<html lang="en">
<head>
<meta charset="utf-8">
<title>Colin Ashford, DDS</title>
<link href="https://fonts.googleapis.com/css2?family=Open+Sans:wght@400;600;700&family=Ubuntu:wght@400;500&display=swap" rel="stylesheet">
<style>
:root{
  --orange:#f07a21;
  --teal:#0e8c9c;
  --teal-dark:#0b6e7a;
  --navy:#0f4c55;
  --ink:#222;
  --grey-text:#8a8a8a;
  --card-grey:#a9a9a9;
  --card-top:#7b7b7b;
  --line:#dcdcdc;
  --panel:#f3f3f3;
  --footer:#2b2b2b;
  --footer-base:#1f1f1f;
  --accent-line:#7ccbd6;
}
*{box-sizing:border-box;margin:0;padding:0}
html,body{width:917px;height:1200px;overflow:hidden;background:#fff}
body{position:relative;font-family:"Open Sans",sans-serif;color:var(--ink)}
.abs{position:absolute}

.topbar{left:0;top:0;width:917px;height:4px;background:var(--orange)}
.site-header{left:0;top:4px;width:917px;height:82px;border-bottom:1px solid var(--line)}
.brand{left:84px;top:34px;font-family:"Ubuntu",sans-serif;font-size:21px;font-weight:500;color:var(--navy);letter-spacing:-.2px}
.brand span{color:var(--navy)}
.nav a{position:absolute;top:41px;font-size:11px;font-weight:600;color:var(--ink);text-decoration:none}
.nav .active{left:343px;top:0;width:69px;height:66px;background:var(--orange);color:#fff;border-radius:0 0 3px 3px;text-align:center;line-height:16px;padding-top:41px;font-weight:400}
.caret{font-size:7px;margin-left:2px}

.hero{left:0;top:86px;width:917px;height:283px;background:linear-gradient(90deg,#f4f8fb,#eef4f9 60%,#f5f8fb)}
.hero-photo{left:0;top:0;width:520px;height:283px;background:linear-gradient(120deg,#dfe9f1 0%,#c9dbe8 35%,#a9cbe4 60%,#e6eef5 100%)}
.tag{background:#333;color:#fff;font-family:"Ubuntu",sans-serif;white-space:nowrap;padding-left:6px}
.tag-main{left:366px;top:93px;width:355px;height:36px;font-size:22px;line-height:36px}
.tag-main em{font-style:normal;color:var(--orange)}
.tag-sub{left:366px;top:137px;width:332px;height:35px;font-size:16px;line-height:35px;padding-left:10px}

.appointment{left:84px;top:370px;width:748px;height:86px;background:var(--panel);border:1px solid var(--line)}
.appointment h2{position:absolute;left:10px;top:10px;font-family:"Ubuntu",sans-serif;font-weight:400;font-size:17.5px;color:var(--navy)}
.appointment p{position:absolute;left:11px;top:39px;width:185px;font-size:9px;line-height:13.5px;color:var(--grey-text)}
.field{position:absolute;width:173px;height:24px;background:#fff;border:1px solid #d8d8d8;border-radius:2px;font-size:8.5px;color:#999;padding:7px 7px 0}
.field .arrow{position:absolute;right:8px;top:9px;width:0;height:0;border-left:3px solid transparent;border-right:3px solid transparent;border-top:4px solid #999}
.btn-appoint{position:absolute;left:607px;top:15px;width:136px;height:58px;background:var(--teal);border-bottom:3px solid var(--teal-dark);border-radius:2px;color:#fff;font-family:"Ubuntu",sans-serif;font-size:19px;line-height:21px;text-align:center;padding-top:8px}

.service{top:486px;width:178px;height:189px;border:1px solid var(--line);border-top:0}
.service .face{height:151px;background:var(--card-grey);border-top:5px solid var(--card-top);display:flex;align-items:center;justify-content:center}
.service.active .face{background:var(--orange);border-top-color:#c95a12}
.service .label{height:37px;line-height:37px;text-align:center;font-size:11px;color:#666;letter-spacing:.2px}
.service.active .label{color:var(--orange)}

.section-title{left:83px;top:703px;font-family:"Ubuntu",sans-serif;font-size:15px;color:#666}
.rule{left:84px;top:727px;width:749px;height:1px;background:var(--line)}
.rule-accent{left:84px;top:726px;width:43px;height:3px;background:var(--accent-line)}
.doctor-photo{left:84px;top:740px;width:219px;height:186px;background:linear-gradient(135deg,#eef1f3,#d9e1e6 50%,#f2f4f6);border:1px solid #e3e3e3}
.doctor{left:330px;top:741px;width:445px}
.doctor h3{font-family:"Ubuntu",sans-serif;font-weight:400;font-size:15px;color:#666}
.doctor h3 em{font-style:normal;color:var(--orange)}
.doctor p{font-size:9.6px;line-height:15.2px;color:var(--grey-text);margin-top:2px}
.doctor h4{font-family:"Ubuntu",sans-serif;font-weight:400;font-size:15px;color:#666;margin:11px 0 13px}
.btn-more{left:330px;top:895px;width:76px;height:25px;background:var(--teal);border-bottom:2px solid var(--teal-dark);color:#fff;font-size:10.5px;line-height:24px;text-align:center;border-radius:1px}

.site-footer{left:0;top:959px;width:917px;height:217px;background:var(--footer);color:#fff}
.site-footer h5{position:absolute;font-family:"Ubuntu",sans-serif;font-weight:400;font-size:14px}
.vline{position:absolute;top:59px;width:1px;height:98px;background:#444}
.post{position:absolute;left:84px;width:180px;height:30px}
.post .thumb{position:absolute;left:0;top:0;width:55px;height:39px;background:linear-gradient(135deg,#9fb9c6,#d7e3e9)}
.post b{position:absolute;left:61px;top:7px;font-size:10px;font-weight:600}
.post small{position:absolute;left:62px;top:24px;font-size:7px}
.sitemap{position:absolute;left:315px;top:53px;list-style:none;font-size:9.6px;line-height:15.3px}
.sitemap .current{color:var(--accent-line);font-weight:700}
.contact-text{position:absolute;left:468px;top:55px;width:160px;font-size:8.3px;line-height:11.5px}
.contact-row{position:absolute;left:468px;font-size:9.6px;display:flex;align-items:center;gap:6px}
.qfield{position:absolute;left:677px;width:156px;background:#fff;border-radius:1px;font-size:8.5px;color:#999;padding:5px 6px}
.btn-send{position:absolute;left:768px;top:181px;width:65px;height:24px;background:var(--orange);color:#fff;font-size:11px;line-height:24px;text-align:center}
.copyright{left:0;top:1176px;width:917px;height:24px;background:var(--footer-base);color:#fff;font-size:9.6px;line-height:24px;text-align:center}
</style>
</head>
<body>
<div class="abs topbar"></div>
<header class="abs site-header">
  <div class="abs brand">Colin Ashford, DDS</div>
  <nav class="nav">
    <a class="active" href="#">HOME</a>
    <a style="left:426px" href="#">About Us</a>
    <a style="left:497px" href="#">Procedures<span class="caret">&#8964;</span></a>
    <a style="left:579px" href="#">Blog</a>
    <a style="left:626px" href="#">Portfolio</a>
    <a style="left:695px" href="#">Patient Info</a>
    <a style="left:778px" href="#">Contact Us</a>
  </nav>
</header>

<section class="abs hero">
  <div class="abs hero-photo" role="img" aria-label="Photo of the dentist in a white coat with a stethoscope, staff and a smiling patient in a bright clinic"></div>
  <div class="abs tag tag-main">I specialize in <em>General Dentistry</em></div>
  <div class="abs tag tag-sub">Lorem ipsum dolor sit amet consectetur</div>
</section>

<section class="abs appointment">
  <h2>Make An Appointment</h2>
  <p>Lorem ipsum dolor sit amet, consectetur adipisicing elit sed do eiusmod tempor ut labore et dolore magna aliqua.</p>
  <div class="field" style="left:236px;top:15px">Name</div>
  <div class="field" style="left:420px;top:14px">E-mail Adderss</div>
  <div class="field" style="left:236px;top:49px">Phone Number</div>
  <div class="field" style="left:420px;top:48px">Appointment Data<span class="arrow"></span></div>
  <div class="btn-appoint">Make<br>Appointment</div>
</section>

<div class="abs service active" style="left:84px">
  <div class="face"><svg width="42" height="54" viewBox="0 0 42 54"><path d="M21 6c-6-5-18-4-19 8-1 9 4 14 6 24 1 8 3 13 6 13 3 0 3-12 7-12s4 12 7 12c3 0 5-5 6-13 2-10 7-15 6-24-1-12-13-13-19-8z" fill="#fff"/><path d="M9 14c4-4 9-2 12 1 3-3 8-5 12-1" stroke="#f07a21" stroke-width="3" fill="none"/></svg></div>
  <div class="label">RESTORATIVE</div>
</div>
<div class="abs service" style="left:274px">
  <div class="face"><svg width="78" height="28" viewBox="0 0 78 28"><rect x="2" y="2" width="74" height="24" rx="10" fill="none" stroke="#fff" stroke-width="3"/><path d="M10 14h58M16 4v20M25 4v20M34 4v20M43 4v20M52 4v20M61 4v20" stroke="#fff" stroke-width="2.5"/></svg></div>
  <div class="label">COSMETIC</div>
</div>
<div class="abs service" style="left:465px">
  <div class="face"><svg width="90" height="36" viewBox="0 0 90 36"><path d="M2 4c20 6 66 6 86 0-10 18-24 30-43 30S12 22 2 4z" fill="#fff"/><path d="M12 9h66" stroke="#a9a9a9" stroke-width="2"/></svg></div>
  <div class="label">PREVENTIVE</div>
</div>
<div class="abs service" style="left:655px">
  <div class="face"><svg width="60" height="62" viewBox="0 0 60 62"><path d="M28 3c10-3 18 7 16 15 10 3 12 18 2 22-8 3-14-4-20 4-4 6-10 17-20 14 8-8 12-20 10-32-2-12 4-21 12-23z" fill="#fff"/></svg></div>
  <div class="label">REPLACEMENT</div>
</div>

<h2 class="abs section-title">Doctors</h2>
<div class="abs rule"></div>
<div class="abs rule-accent"></div>
<div class="abs doctor-photo" role="img" aria-label="Portrait photo of the doctor in a white coat in a dental treatment room"></div>
<article class="abs doctor">
  <h3>Doctors <em>Colin Ashford, DDS</em></h3>
  <p>Lorem ipsum dolor sit amet, consectetur adipisicing elit, sed do eiusmod tempor incididunt ut labore et dolore magna aliqua. Ut enim ad minim veniam, quis nostrud exercitation ullamco laboris nisi ut aliquip ex ea commodo consequat.</p>
  <h4>fugiat nulla pariatur</h4>
  <p>Excepteur sint occaecat cupidatat non proident, sunt in culpa qui officia deserunt mollit anim id est laborum...</p>
</article>
<div class="abs btn-more">Read More</div>

<footer class="abs site-footer">
  <h5 style="left:83px;top:29px">Latest From The Blog</h5>
  <h5 style="left:315px;top:27px">Site Map</h5>
  <h5 style="left:468px;top:27px">Contact Info</h5>
  <h5 style="left:676px;top:27px">Quick Contact</h5>
  <div class="vline" style="left:274px"></div>
  <div class="vline" style="left:424px"></div>
  <div class="vline" style="left:638px"></div>

  <div class="post" style="top:57px"><div class="thumb" role="img" aria-label="Blog thumbnail: surgeon in cap"></div><b>Hello world</b><small>June 03,2014</small></div>
  <div class="post" style="top:109px"><div class="thumb" role="img" aria-label="Blog thumbnail: dentist with mask"></div><b>Hello world</b><small>June 03,2014</small></div>

  <ul class="sitemap">
    <li class="current">Home</li><li>About Us</li><li>Procedures</li><li>Blog</li><li>Portfolio</li><li>Patient Info</li><li>Contact Us</li>
  </ul>

  <p class="contact-text">Lorem ipsum dolor sit amet, consectetur adipisicing elit, sed do eiusmod tempor incididunt.</p>
  <div class="contact-row" style="top:99px"><svg width="10" height="12" viewBox="0 0 10 12"><path d="M5 0a4 4 0 0 0-4 4c0 3 4 8 4 8s4-5 4-8a4 4 0 0 0-4-4z" fill="#fff"/><circle cx="5" cy="4" r="1.5" fill="#2b2b2b"/></svg>lorem ipsum street</div>
  <div class="contact-row" style="top:119px"><svg width="10" height="10" viewBox="0 0 10 10"><path d="M1 3c0-2 8-2 8 0v1H7V3H3v1H1z M2 5h6l1 4H1z" fill="#fff"/></svg>+1 (555) 321 0148</div>
  <div class="contact-row" style="top:138px"><svg width="10" height="8" viewBox="0 0 10 8"><rect width="10" height="8" fill="#fff"/><path d="M0 0l5 4 5-4" stroke="#2b2b2b" fill="none"/></svg>info@ashforddental.com</div>

  <div class="qfield" style="top:59px;height:24px">Name</div>
  <div class="qfield" style="top:88px;height:24px">E-mail</div>
  <div class="qfield" style="top:118px;height:55px">Message</div>
  <div class="btn-send">Send</div>
</footer>
<div class="abs copyright">Copy Right © 2014 ColinAshford,dds. All Rights Reserved.</div>
</body>
</html>
```